Verodex business card

Business card for sustainable investment company called "Verodex". Verodex is an exchange platform selling carbon credits between buyers and sellers. Carbon Credits are an environmental commodity for reducing global carbon emissions.

the card should obviously have our logo and the theme should be sustainability/environment mixed with a trading platform.

Contact Information for Business Card

Logo, Name, Title, Phone, Email

Colors
0054AA
0677BA
7BADD7
CADEEF
E8F1F8
0094D4
00A9DD
6FCCEA
C7EBF8
E9F6FB
00AB8E
00BBA5
67D7C9
C6EFE9
E9F9F6
59FF00
82FF00
B8FF75
E3FFCB
F4FFEA

```html
<!DOCTYPE html>
<html lang="en">
<head>
<meta charset="utf-8">
<title>Verodex business card</title>
<link rel="stylesheet" href="https://fonts.googleapis.com/css2?family=Inter:wght@400;600;700&family=Montserrat:wght@600&display=swap">
<style>
  :root {
    --page: #e4e4e4;
    --navy: #22334d;
    --navy-light: #33445e;
    --paper: #f5f5f7;
    --ink: #1f2c40;
    --blue: #1f73e0;
    --cyan: #1ec8ea;
  }
  html, body {
    margin: 0;
    width: 1200px;
    height: 1200px;
    overflow: hidden;
    background: var(--page);
  }
  .canvas {
    position: relative;
    width: 1200px;
    height: 1200px;
  }
  .card {
    position: absolute;
    left: 200px;
    width: 800px;
    height: 457px;
    border-radius: 30px;
    overflow: hidden;
  }
  .card--front { top: 88px; background: var(--navy); }
  .card--back {
    top: 655px;
    background: linear-gradient(180deg, var(--navy-light) 0%, var(--navy) 100%);
    display: flex;
    align-items: center;
    justify-content: center;
  }
  .card__hexagon {
    position: absolute;
    inset: 0;
    width: 100%;
    height: 100%;
  }
  .front-content {
    position: absolute;
    inset: 0;
    text-align: center;
    font-family: "Inter", sans-serif;
    color: var(--ink);
  }
  .brand {
    position: absolute;
    top: 108px;
    left: 0;
    right: 0;
    display: flex;
    align-items: center;
    justify-content: center;
    gap: 16px;
  }
  .brand__mark {
    width: 34px;
    height: 34px;
    background: var(--blue);
  }
  .brand__name {
    font-family: "Montserrat", sans-serif;
    font-weight: 600;
    font-size: 40px;
    letter-spacing: 0.5px;
    color: var(--ink);
  }
  .person__name {
    position: absolute;
    top: 214px;
    left: 0; right: 0;
    font-size: 30px;
    font-weight: 600;
    color: var(--blue);
  }
  .person__title {
    position: absolute;
    top: 252px;
    left: 0; right: 0;
    font-size: 21px;
    font-weight: 700;
    color: var(--ink);
  }
  .contact {
    position: absolute;
    left: 0; right: 0;
    display: flex;
    align-items: center;
    justify-content: center;
    gap: 6px;
    font-size: 21px;
    font-weight: 400;
    color: var(--ink);
  }
  .contact--phone { top: 305px; }
  .contact--email { top: 332px; }
  .contact__icon { width: 18px; height: 18px; fill: var(--blue); }
  .back-name {
    font-family: "Montserrat", sans-serif;
    font-weight: 600;
    font-size: 84px;
    letter-spacing: 3px;
    color: #ffffff;
  }
</style>
</head>
<body>
<main class="canvas">
  <section class="card card--front">
    <svg class="card__hexagon" viewBox="0 0 800 457" preserveAspectRatio="none" aria-hidden="true">
      <polygon points="204,0 604,0 732,228 604,457 204,457 72,228" fill="var(--paper)"/>
    </svg>
    <div class="front-content">
      <div class="brand">
        <span class="brand__mark"></span>
        <span class="brand__name">VERODEX</span>
      </div>
      <div class="person__name">Daniel Reeves</div>
      <div class="person__title">President</div>
      <div class="contact contact--phone">
        <svg class="contact__icon" viewBox="0 0 24 24" aria-hidden="true"><path d="M6.6 10.8a15.1 15.1 0 0 0 6.6 6.6l2.2-2.2c.3-.3.7-.4 1-.2 1.1.4 2.3.6 3.6.6.6 0 1 .4 1 1V20c0 .6-.4 1-1 1C10.6 21 3 13.4 3 4c0-.6.4-1 1-1h3.5c.6 0 1 .4 1 1 0 1.3.2 2.5.6 3.6.1.3 0 .7-.2 1l-2.3 2.2z"/></svg>
        <span>(415) 2906-7318</span>
      </div>
      <div class="contact contact--email">
        <svg class="contact__icon" viewBox="0 0 24 24" aria-hidden="true"><path d="M3 6h18v12H3z M3 6l9 7 9-7" fill="var(--blue)" stroke="var(--paper)" stroke-width="1.5"/></svg>
        <span>info@verodex.com</span>
      </div>
    </div>
  </section>

  <section class="card card--back">
    <span class="back-name">VERODEX</span>
  </section>
</main>
</body>
</html>
```